Business Cards Needed for Innovative Healthcare Marketing Company

We are a marketing company focused on healthcare. Our company is all about rebranding yourself renewing your image and generating results. The phoenix stands for "reborn" or "rising" which we provide new brands for our clients we take their old brands and renew it with creativity and innovation. I am looking for a business card with color dimension. I have attached an example of a card I think has the look and feel of what I am trying to accomplish. I like that the card example has black and grey font colors, I like the font placement and the small logo, I really like the use of the colors on the right those are the colors of my logo. My logo is phoenix so maybe incorporating flames similar to that design. I would like the back a solid color maybe red with an opaque version of the logo and website. As a marketing company I am always open to creative liberty!

Target Market(s)

Doctors and business professionals.

Industry/Entity Type

Marketing

Contact Information for Business Card

Valcorne Health Care Marketing
Marla Tenwick- CEO
#(512)638-2974
email-marla@valcorne.com
website- valcorne.com

Font styles to use
Sans Serif

Colors
ec1f27
f37122
ffc214
fbed22
fbf289
f04a50

Requirements
Must have
• The logo and required information
Nice to have
• icons by the information
Should not have
• child like font

```html
<!DOCTYPE html>
<html lang="en">
<head>
<meta charset="utf-8">
<title>Valcorne Healthcare Marketing – Business Card</title>
<link rel="stylesheet" href="https://fonts.googleapis.com/css2?family=Open+Sans:wght@300;400;700&display=swap">
<style>
  :root {
    --backdrop: #ebe7e2;
    --card-white: #ffffff;
    --brand-red: #a3221f;
    --deep-red: #9e1c20;
    --flame-orange: #f39322;
    --ember-orange: #e8731f;
    --ink: #2b2b2b;
    --rule: #c9c9c9;
    --faint-mark: #f1f1f1;
  }
  * { margin: 0; padding: 0; box-sizing: border-box; }
  html, body {
    width: 1200px; height: 1000px; overflow: hidden;
    background: var(--backdrop);
    font-family: "Open Sans", Arial, sans-serif;
  }
  .card {
    position: absolute; left: 265px; width: 666px; height: 397px;
    border-radius: 24px; overflow: hidden;
    box-shadow: 0 4px 14px rgba(0,0,0,.18);
  }
  .card--front { top: 73px; background: var(--card-white); }
  .card--back {
    top: 532px;
    background: radial-gradient(circle at 25% 50%, var(--flame-orange) 0%, var(--ember-orange) 30%, var(--deep-red) 75%);
  }
  .faint-mark {
    position: absolute; border-radius: 50%;
  }
  .card--front .faint-mark {
    left: 0; top: 40px; width: 320px; height: 260px;
    background: radial-gradient(ellipse at center, var(--faint-mark) 0%, rgba(241,241,241,0) 70%);
  }
  .card--back .faint-mark {
    left: 10px; top: 40px; width: 360px; height: 340px;
    background: radial-gradient(ellipse at center, rgba(255,200,120,.28) 0%, rgba(255,200,120,0) 70%);
  }
  .brand-name {
    position: absolute; text-align: left; font-weight: 400; line-height: 1;
  }
  .brand-name .brand-word { display: block; font-size: 48px; letter-spacing: 1px; }
  .brand-name .brand-tag { display: block; font-size: 17px; letter-spacing: .5px; margin-top: 10px; }
  .brand-name .brand-dot {
    position: absolute; left: -58px; top: 4px; width: 44px; height: 44px; border-radius: 50%;
  }
  .card--front .brand-name { right: 32px; top: 54px; color: var(--brand-red); }
  .card--front .brand-dot { background: var(--flame-orange); }
  .card--back .brand-name { right: 32px; top: 286px; color: #ffffff; }
  .card--back .brand-dot { background: #ffffff; }
  .person-name {
    position: absolute; left: 33px; top: 176px;
    color: var(--brand-red); font-weight: 700; font-size: 21px; letter-spacing: .3px;
  }
  .person-role { position: absolute; left: 33px; top: 204px; font-size: 16px; color: var(--ink); }
  .divider { position: absolute; left: 33px; top: 239px; width: 450px; height: 1px; background: var(--rule); }
  .address { position: absolute; left: 33px; top: 251px; font-size: 16px; line-height: 24px; color: var(--ink); }
  .contact-list {
    position: absolute; right: 30px; top: 227px; list-style: none; text-align: right;
    font-size: 16px; line-height: 27px; color: var(--ink);
  }
  .contact-list svg { width: 14px; height: 12px; margin-left: 6px; vertical-align: -1px; fill: var(--brand-red); }
  .wave { position: absolute; left: 0; top: 0; width: 666px; height: 397px; }
  .website {
    position: absolute; right: 31px; top: 350px; color: #fff; font-size: 16px; letter-spacing: .4px;
  }
</style>
</head>
<body>
  <section class="card card--front">
    <div class="faint-mark" role="img" aria-label="Faint brand emblem watermark"></div>
    <div class="brand-name">
      <span class="brand-dot"></span>
      <span class="brand-word">VALCORNE</span>
      <span class="brand-tag">HEALTHCARE MARKETING</span>
    </div>
    <p class="person-name">MARLA TENWICK</p>
    <p class="person-role">CEO</p>
    <div class="divider"></div>
    <p class="address">Level 14, 8 Harlow House<br>Westbury, 20, North Vale</p>
    <ul class="contact-list">
      <li>(512)638-2974<svg viewBox="0 0 14 12"><path d="M1 4c0-2 3-3 6-3s6 1 6 3v1h-3V4H4v1H1zM3 6h8l2 5H1z"/></svg></li>
      <li>marla@valcorne.com<svg viewBox="0 0 14 12"><path d="M0 2h14v9H0zM1 3l6 4 6-4" stroke="#fff" stroke-width="1"/></svg></li>
    </ul>
    <svg class="wave" viewBox="0 0 666 397" aria-hidden="true">
      <defs>
        <linearGradient id="bandGradient" x1="0" x2="1" y1="0" y2="0">
          <stop offset="0" stop-color="#f7941d"/>
          <stop offset=".55" stop-color="#e06a1f"/>
          <stop offset="1" stop-color="#b3281f"/>
        </linearGradient>
      </defs>
      <path d="M0 318 C120 330 260 352 350 346 C240 358 110 356 0 346 Z" fill="var(--brand-red)"/>
      <path d="M0 352 C160 370 300 372 420 348 C520 328 610 318 666 328 L666 397 L0 397 Z" fill="url(#bandGradient)"/>
    </svg>
    <p class="website">www.valcorne.com</p>
  </section>

  <section class="card card--back">
    <div class="faint-mark" role="img" aria-label="Large translucent brand emblem decoration"></div>
    <div class="brand-name">
      <span class="brand-dot"></span>
      <span class="brand-word">VALCORNE</span>
      <span class="brand-tag">HEALTHCARE MARKETING</span>
    </div>
  </section>
</body>
</html>
```